Vindgerdi - Start-up company selling electricity

Hello let me tell you about Vindgerdi.

Vindgerdi is start-up company selling electricity in Iceland. The operations of the company consist of making power usage forecasts for our customers, purchasing the electricity wholesale from the energy producers, and selling the electricity to the consumer. We are focused on tech by using optimization and machine learning to minimize electricity prices to our customers. Our marketing strategy is to portray a tech company mindset and to show dedication to driving down the electricity price on the market.

We need your help to make our website pop. Possible concepts to work with are as follows:

- Iceland the land of ice and fire
- Green energy
- Innovation
- Tech and data science

Link to our website: https://prufa.vindgerdi-example.is/
We are open to ideas.
Thank you!

Target Market(s)

Electricity consumers both homes and companies.

Number of Pages Required

1 page

Font styles to use
Serif
Sans Serif

```html
<!DOCTYPE html>
<html lang="en">
<head>
<meta charset="utf-8">
<title>Vindgerdi – Electricity for everyone</title>
<link href="https://fonts.googleapis.com/css2?family=Lora:wght@400;700&family=Open+Sans:wght@400;600;700&display=swap" rel="stylesheet">
<style>
:root{
  --navy:#14213d;
  --red:#9b1c1f;
  --red-dark:#7d1416;
  --red-card:#a82427;
  --white:#ffffff;
  --ink:#2b2f3a;
  --muted:#6b7080;
  --accent:#e0343a;
}
*{margin:0;padding:0;box-sizing:border-box}
html,body{width:1200px;height:2488px;overflow:hidden;background:var(--white)}
body{position:relative;font-family:"Open Sans",Arial,sans-serif;color:var(--ink)}

.backdrop{position:absolute;left:0;top:0;width:1200px;height:2488px}

/* header */
.site-header{position:absolute;left:0;top:0;width:1200px;height:90px;z-index:2}
.brand{position:absolute;left:128px;top:30px;display:flex;align-items:center;gap:10px;
  font-family:"Lora",Georgia,serif;font-weight:700;font-size:26px;color:var(--red);letter-spacing:1px}
.brand-dot{width:22px;height:22px;border-radius:50%;background:var(--navy)}
.main-nav{position:absolute;left:470px;top:40px;display:flex;gap:32px;font-size:14px;color:var(--navy)}
.main-nav a{color:inherit;text-decoration:none}
.main-nav a.active{border-bottom:2px solid var(--red);padding-bottom:4px;color:var(--red)}

/* hero */
.hero-title{position:absolute;left:128px;top:160px;font-family:"Lora",Georgia,serif;font-weight:700;
  font-size:76px;letter-spacing:2px;color:var(--red)}
.hero-lead{position:absolute;left:130px;top:276px;width:400px;font-family:"Lora",Georgia,serif;
  font-size:19px;line-height:1.45;color:var(--navy)}
.btn{display:inline-block;border-radius:22px;font-size:13px;font-weight:700;letter-spacing:.5px;
  text-align:center;text-decoration:none}
.btn-red{background:var(--red);color:var(--white)}
.btn-navy{background:var(--navy);color:var(--white)}
.btn-outline{border:2px solid var(--red);color:var(--red);background:var(--white)}
.hero-cta{position:absolute;left:140px;top:386px;width:148px;height:42px;line-height:42px}
.hero-photo{position:absolute;left:760px;top:80px;width:400px;height:400px;border-radius:50%;
  background:radial-gradient(circle at 60% 35%,#e7a25a 0%,#7d5a78 35%,#2a3566 70%,#131d3a 100%)}
.slider-dots{position:absolute;left:560px;top:510px;display:flex;gap:8px}
.slider-dots span{width:9px;height:9px;border-radius:50%;background:#c9cad1}
.slider-dots span.on{background:var(--navy)}

/* unique position */
.position{position:absolute;left:0;top:1010px;width:1200px;text-align:center;color:var(--white)}
.position h2{font-weight:700;font-size:30px;letter-spacing:1px;line-height:1.3}
.position h2 .accent{display:block;color:var(--accent)}
.position p{width:880px;margin:20px auto 0;font-family:"Lora",Georgia,serif;font-size:14px;line-height:1.6;color:#d8dbe5}

/* cards */
.card{position:absolute;top:1400px;height:360px;border-radius:16px;background:var(--red-card);
  box-shadow:0 10px 30px rgba(60,0,0,.35);color:var(--white);overflow:hidden}
.card-welcome{left:140px;width:300px;text-align:center}
.card-prices{left:462px;width:300px;padding:36px 28px}
.card-future{left:784px;width:290px}
.welcome-mark{width:86px;height:86px;border-radius:50%;background:var(--navy);margin:46px auto 0}
.card h3{font-family:"Lora",Georgia,serif;font-weight:700;color:var(--white)}
.card-welcome h3{font-size:22px;margin-top:40px}
.card-welcome .btn{width:170px;height:40px;line-height:36px;margin-top:14px}
.card-welcome .btn-navy{line-height:40px;margin-top:12px}
.card-prices h3{font-size:34px}
.price-row{display:flex;gap:34px;margin-top:26px}
.price{font-family:"Lora",Georgia,serif;font-size:32px;font-weight:700}
.price small{display:block;font-family:"Open Sans",Arial,sans-serif;font-size:11px;font-weight:400;opacity:.85;line-height:1.4}
.card-prices h4{font-family:"Lora",Georgia,serif;font-size:17px;margin-top:26px}
.card-prices .btn{width:170px;height:40px;line-height:40px;margin-top:26px}
.future-photo{height:150px;background:radial-gradient(circle at 50% 55%,#f4f0ff 0%,#b45cf0 18%,#3a3fb8 45%,#141a4a 75%,#0b0f2a 100%)}
.card-future h3{font-size:22px;margin:30px 24px 0}
.card-future p{margin:14px 24px 0;font-size:12.5px;line-height:1.55;opacity:.9}

/* footer */
.site-footer{position:absolute;left:0;top:2190px;width:1200px;text-align:center}
.footer-brand{display:inline-flex;align-items:center;gap:12px;font-family:"Lora",Georgia,serif;
  font-weight:700;font-size:40px;color:var(--red);letter-spacing:1px}
.footer-brand .brand-dot{width:34px;height:34px}
.contact-row{display:flex;justify-content:center;gap:28px;margin-top:40px;font-size:13px;color:var(--ink)}
.contact-row span{display:flex;align-items:center;gap:8px}
.contact-row svg{width:14px;height:14px}
.company-ids{margin-top:16px;font-size:13px;font-weight:700;color:var(--navy)}
.copyright{margin-top:14px;font-size:11px;color:var(--muted)}
.social{display:flex;justify-content:center;gap:12px;margin-top:22px}
.social span{width:30px;height:30px;border-radius:50%;background:var(--red)}
</style>
</head>
<body>

<svg class="backdrop" viewBox="0 0 1200 2488" aria-hidden="true">
  <polygon points="0,600 0,1400 1200,1360 1200,760 760,560 560,780 420,690" fill="var(--navy)"/>
  <polyline points="0,640 420,730 560,820 760,600 1200,800" fill="none" stroke="var(--white)" stroke-width="14"/>
  <polygon points="0,1370 1200,1330 1200,2060 660,2000 520,2120 0,2040" fill="var(--red)"/>
  <polygon points="0,1370 1200,1330 1200,1342 0,1382" fill="var(--red-dark)" opacity=".6"/>
  <polyline points="0,2070 520,2150 660,2030 1200,2090" fill="none" stroke="var(--red)" stroke-width="6"/>
</svg>

<header class="site-header">
  <div class="brand"><span class="brand-dot"></span>VINDGERDI</div>
  <nav class="main-nav">
    <a class="active" href="#">Terms of business</a>
    <a href="#">Questions &amp; answers</a>
    <a href="#">About Vindgerdi</a>
  </nav>
</header>

<section class="hero">
  <h1 class="hero-title">VINDGERDI</h1>
  <p class="hero-lead">Our goal is to minimize the cost of energy sales,promote energy balance and offer good service.</p>
  <a class="btn btn-red hero-cta" href="#">GET STARTED ➜</a>
  <div class="hero-photo" role="img" aria-label="Photograph of an electricity pylon against a dusk sky"></div>
  <div class="slider-dots"><span class="on"></span><span></span><span></span><span></span></div>
</section>

<section class="position">
  <h2>WHAT IS VINDGERDI'S UNIQUE POSITION<span class="accent">IN THE ELECTRICITY SALES MARKET?</span></h2>
  <p>Vindgerdi uses automation and artificial intelligence to achieve lower prices in the electricity market. Our goal is to minimize the cost of energy sales, promote energy balance and offer good service.</p>
  <p>Vindgerdi's goal is to offer its customers the most favorable electricity price in Iceland. Electricity is part of the monthly costs of households and companies, and by doing business with Vindgerdi, savings can be achieved and operating costs reduced. Vindgerdi wants to make the electricity system "smarter". Data science and the use of artificial intelligence can maximize the efficiency of the electricity system, minimize electricity costs and promote energy balance. Therefore, it can be said that by trading with Vindgerdi, you support the development of the Icelandic electricity market.</p>
</section>

<article class="card card-welcome">
  <div class="welcome-mark"></div>
  <h3>Welcome to business</h3>
  <a class="btn btn-outline" href="#">COMPANY</a><br>
  <a class="btn btn-navy" href="#">HOME</a>
</article>

<article class="card card-prices">
  <h3>Price list</h3>
  <div class="price-row">
    <div class="price">6.95<small>ISK / kWh<br>Home tariff</small></div>
    <div class="price">6.22<small>ISK / kWh<br>Business tariff</small></div>
  </div>
  <h4>Make a price comparison</h4>
  <a class="btn btn-navy" href="#">COMPARE</a>
</article>

<article class="card card-future">
  <div class="future-photo" role="img" aria-label="Photograph of a bright electric lightning spark"></div>
  <h3>The future is exciting</h3>
  <p>Let's make the electricity system smarter together. Vindgerdi uses artificial intelligence, data science and automation to minimize costs and promote electricity.</p>
</article>

<footer class="site-footer">
  <div class="footer-brand"><span class="brand-dot"></span>VINDGERDI</div>
  <div class="contact-row">
    <span><svg viewBox="0 0 14 14"><path d="M7 1a4 4 0 0 1 4 4c0 3-4 8-4 8S3 8 3 5a4 4 0 0 1 4-4z" fill="var(--red)"/><circle cx="7" cy="5" r="1.5" fill="#fff"/></svg>Lindargata 12, 101 Reykjavík</span>
    <span><svg viewBox="0 0 14 14"><rect x="1" y="3" width="12" height="8" rx="1" fill="none" stroke="var(--red)" stroke-width="1.5"/><path d="M1 3l6 5 6-5" fill="none" stroke="var(--red)" stroke-width="1.5"/></svg>hallo@vindgerdi-example.is</span>
    <span><svg viewBox="0 0 14 14"><path d="M3 1h3l1 3-2 1a7 7 0 0 0 4 4l1-2 3 1v3a1 1 0 0 1-1 1A11 11 0 0 1 2 2a1 1 0 0 1 1-1z" fill="var(--red)"/></svg>555-0190</span>
  </div>
  <div class="company-ids">Vindgerdi ehf ID number: 550123-0010 VAT number: 140567</div>
  <div class="copyright">Copyright © Vindgerdi 2021 All rights reserved | Privacy Policy</div>
  <div class="social"><span></span><span></span><span></span></div>
</footer>

</body>
</html>
```